Australian Trucking Company Requires Professional Looking Stationary

We require a professional looking stationary design that incorporates our newly designed logo.

Our business, called "Brell Haulage Contracting", provides contracting work, transport and logistics to business in Western Australia particularly with links to the mining sector.

We are a small business looking to expand and our new logo and our new stationary will help develop our brand image in our market place.

Target Market(s)

Businesses and Corporation with links to the Mining Sector

Industry/Entity Type

Small Business

Requirements
Must have
• The letterhead must have the following details:
The new logo

Text saying: "Brell Holdings Pty Ltd (ACN 582 316 907) ATF The Brell Discretionary Trust T/AS"
"ABN 71 834 209 553"
Address "P.O Box 817 Wattlegrove WA, 6958"
Phone: 08 9352 7140
Email: brellhaul@mailbox-example.com.au

The text on the letterhead should be editable as the details are likely to change in the near future. Provision should be made for a website address all though one isn't available at the moment.

The styling, layout and font text is entirely up to the designer.

```html
<!DOCTYPE html>
<html lang="en">
<head>
<meta charset="utf-8">
<title>Brell Haulage Contracting – Business Card</title>
<link rel="stylesheet" href="https://fonts.googleapis.com/css2?family=Open+Sans:wght@400;600;700;800&display=swap">
<style>
  :root {
    --bg: #ece8e3;
    --card: #ffffff;
    --red: #c8161d;
    --red-dark: #8e0c12;
    --red-bright: #e52329;
    --ink: #1e1e1e;
    --grey: #7a7a7a;
    --rule: #dcdcdc;
  }
  * { margin: 0; padding: 0; box-sizing: border-box; }
  html, body { width: 1200px; height: 426px; overflow: hidden; }
  body {
    background: var(--bg);
    font-family: "Open Sans", Arial, sans-serif;
    color: var(--ink);
    position: relative;
  }
  .card {
    position: absolute;
    background: var(--card);
    border-radius: 20px;
    overflow: hidden;
    box-shadow: 0 2px 6px rgba(0,0,0,.18);
  }
  .card--front { left: 60px; top: 63px; width: 520px; height: 297px; }
  .card--back  { left: 603px; top: 62px; width: 542px; height: 296px; }

  .card__header {
    height: 52px;
    background: linear-gradient(90deg, var(--red-dark) 0%, var(--red-bright) 50%, var(--red-dark) 100%);
    color: #fff;
    display: flex;
    align-items: center;
    justify-content: center;
    gap: 6px;
    border-bottom: 3px solid var(--red-dark);
  }
  .card__name { font-size: 17px; font-weight: 700; }
  .card__role { font-size: 12px; font-weight: 400; }

  .brand {
    position: absolute;
    left: 70px; top: 85px;
    display: flex;
    align-items: center;
    gap: 26px;
  }
  .brand__mark {
    width: 80px; height: 80px;
    border-radius: 50%;
    background: #8a8a8a;
  }
  .brand__name {
    font-size: 27px;
    font-weight: 800;
    line-height: 27px;
    color: var(--red);
    text-transform: uppercase;
    letter-spacing: .5px;
  }

  .contact {
    position: absolute;
    left: 0; right: 0; top: 200px;
    text-align: center;
    font-size: 12px;
    line-height: 21px;
  }
  .contact__row { display: flex; justify-content: center; align-items: center; gap: 10px; }
  .contact__item { display: inline-flex; align-items: center; gap: 4px; }
  .contact__icon { width: 11px; height: 11px; fill: var(--ink); }

  .card__rule {
    position: absolute;
    left: 55px; right: 55px; top: 244px;
    height: 1px;
    background: var(--rule);
  }
  .legal {
    position: absolute;
    left: 0; right: 0; top: 253px;
    text-align: center;
    font-size: 11px;
    line-height: 18px;
  }

  .card--back .brand {
    left: 0; right: 0; top: 0; bottom: 0;
    justify-content: center;
    gap: 22px;
  }
  .card--back .brand__mark { width: 96px; height: 96px; background: var(--red); }
  .card--back .brand__name { font-size: 32px; line-height: 33px; }
</style>
</head>
<body>
  <section class="card card--front">
    <header class="card__header">
      <span class="card__name">Persons name,</span>
      <span class="card__role">Manager</span>
    </header>

    <div class="brand">
      <span class="brand__mark"></span>
      <div class="brand__name">Brell<br>Haulage<br>Contracting</div>
    </div>

    <div class="contact">
      <div class="contact__row">
        <span class="contact__item">
          <svg class="contact__icon" viewBox="0 0 24 24"><path d="M6.6 10.8a15 15 0 0 0 6.6 6.6l2.2-2.2c.3-.3.7-.4 1-.2 1.1.4 2.3.6 3.6.6.6 0 1 .4 1 1V20c0 .6-.4 1-1 1A17 17 0 0 1 3 4c0-.6.4-1 1-1h3.5c.6 0 1 .4 1 1 0 1.3.2 2.5.6 3.6.1.3 0 .7-.2 1z"/></svg>
          08 9352 7140
        </span>
        <span class="contact__item">
          <svg class="contact__icon" viewBox="0 0 24 24"><path d="M2 5h20v14H2z" fill="none" stroke="#1e1e1e" stroke-width="2"/><path d="M2 5l10 8 10-8" fill="none" stroke="#1e1e1e" stroke-width="2"/></svg>
          brellhaul@mailbox-example.com.au
        </span>
      </div>
      <div class="contact__row">
        <span class="contact__item">
          <svg class="contact__icon" viewBox="0 0 24 24"><path d="M12 3l10 9h-3v9h-5v-6h-4v6H5v-9H2z"/></svg>
          P.O Box 817 Wattlegrove WA, 6958
        </span>
      </div>
    </div>

    <div class="card__rule"></div>

    <div class="legal">
      Brell Holdings Pty Ltd (ACN 582 316 907) ATF The Brell Discretionary Trust T/AS<br>
      ABN 71 834 209 553
    </div>
  </section>

  <section class="card card--back">
    <div class="brand">
      <span class="brand__mark"></span>
      <div class="brand__name">Brell<br>Haulage<br>Contracting</div>
    </div>
  </section>
</body>
</html>
```